Design for three pages of a 12-page 4-color 8.5 x 11 magazine-type booklet

We will be taking the information from a webpage at brightmeadowcivic.org and putting it into a 12-page 4-color 8.5 x 11 magazine-type booklet that will look like an upscale company report. I need to have a design in Photoshop for the cover and two inside pages that I can use as the template for the pages. I likely will also need help putting it together once I start putting the contents into the pages. I may just decide on the content and have the designer create the booklet as an additional freelance contract. First, I need a design for (1) the front cover, (2) one information page taken from information on http://www.brightmeadowcivic.org/bmci-project-management-staff/, and (3) one of the pages that has a researcher from this page on it: http://www.brightmeadowcivic.org/teaching-people-how-to-have/. That's designs for three pages. The designs have to be very professional looking and businesslike. We will be using the booklet to pitch to foundations and philanthropists. The work on the publication itself would be additional freelance work on an hourly basis.

Font styles to use
Serif

Colors

Designer to choose colors to be used in the design.

Requirements
Must have
• Professional look

```html
<!DOCTYPE html>
<html lang="en">
<head>
<meta charset="utf-8">
<title>BMCI Booklet – Inside Spread</title>
<link rel="stylesheet" href="https://fonts.googleapis.com/css2?family=Titillium+Web:ital,wght@0,300;0,400;0,600;0,700;1,600&display=swap">
<style>
  :root {
    --indigo: #3a3891;
    --indigo-deep: #2f2d7c;
    --ink: #3a3a3f;
    --muted: #6a6a72;
    --paper: #f4f4f5;
    --backdrop: #dfe2e4;
    --rule: #3a3891;
  }
  * { box-sizing: border-box; margin: 0; padding: 0; }
  html, body { width: 1200px; height: 840px; overflow: hidden; }
  body {
    background: var(--backdrop);
    font-family: "Titillium Web", sans-serif;
    color: var(--ink);
  }
  .spread {
    position: absolute; left: 75px; top: 31px;
    width: 1050px; height: 778px;
    display: flex;
    box-shadow: 0 6px 24px rgba(0,0,0,.18);
  }
  .page {
    position: relative; width: 525px; height: 778px;
    background: var(--paper); overflow: hidden;
  }

  /* ---------- Staff page ---------- */
  .staff-title {
    position: absolute; left: 28px; top: 42px;
    font-size: 23px; font-weight: 600; letter-spacing: -.2px; color: #2e2e33;
  }
  .title-bar {
    position: absolute; left: 28px; top: 86px; width: 457px; height: 5px;
    background: linear-gradient(90deg, var(--indigo-deep), #4a48a8);
  }
  .staff-intro {
    position: absolute; left: 28px; top: 98px; width: 440px;
    font-size: 10.5px; font-weight: 300; line-height: 1.3; color: var(--muted);
  }
  .staff-card { position: absolute; width: 136px; }
  .staff-photo { width: 136px; height: 120px; display: block; }
  .staff-role {
    margin-top: 12px; font-size: 11px; font-weight: 600;
    color: var(--indigo); text-transform: uppercase; letter-spacing: .1px;
  }
  .staff-name {
    font-size: 7.5px; font-style: italic; font-weight: 600; color: #44444a;
    padding-bottom: 5px; border-bottom: 1.5px solid var(--rule); margin-bottom: 6px;
  }
  .staff-bio {
    font-size: 7.4px; font-weight: 300; line-height: 1.35; color: var(--muted);
  }

  .footer-url {
    position: absolute; top: 716px; font-size: 7.5px; font-weight: 600; color: #55555c;
  }
  .footer-bar { position: absolute; top: 713px; height: 16px; }

  /* ---------- Programme page ---------- */
  .hero-photo {
    position: absolute; left: 0; top: 43px; width: 525px; height: 310px;
    background: linear-gradient(135deg, #5d6a77 0%, #9aa4ad 35%, #3b4550 70%, #222a33 100%);
  }
  .hero-banner { position: absolute; left: 0; top: 296px; }
  .hero-heading {
    position: absolute; right: 33px; top: 318px; text-align: right; color: #fff;
    line-height: 1.1;
  }
  .hero-heading .lead { display: block; font-size: 28px; font-weight: 300; }
  .hero-heading .strong { display: block; font-size: 24px; font-weight: 600; text-transform: uppercase; }

  .programme-copy {
    position: absolute; left: 29px; top: 441px; width: 475px;
    font-size: 7.6px; font-weight: 300; line-height: 1.35; color: var(--muted);
  }
  .link-heading {
    position: absolute; left: 29px; top: 497px;
    font-size: 11.5px; font-weight: 600; color: var(--indigo);
  }
  .link-sub {
    position: absolute; left: 29px; top: 511px;
    font-size: 10px; font-weight: 400; color: #55555c;
  }
  .topic {
    position: absolute; display: flex; align-items: center; gap: 9px;
    font-size: 9px; font-weight: 300; color: #55555c; line-height: 1.25;
  }
  .topic svg { flex: none; }
</style>
</head>
<body>
<div class="spread">

  <!-- Staff page -->
  <section class="page staff-page">
    <h1 class="staff-title">BMCI Project Management Staff</h1>
    <div class="title-bar"></div>
    <p class="staff-intro">Humankind will live together in love, peace, and joy when all people grow to have deeply felt love and regard for all others. This profound change in humankind requires transformed lives,one individual at a time.</p>

    <article class="staff-card" style="left:28px; top:183px;">
      <div class="staff-photo" role="img" aria-label="Portrait of the project director" style="background:linear-gradient(160deg,#6b4a2e,#3a2a1c);"></div>
      <h2 class="staff-role">Project Director</h2>
      <p class="staff-name">R. Martin Ellery, PhD</p>
      <p class="staff-bio">Dr. Ellery is the president of BMCI. His PhD is in supervision and developing educational programs. He is the co-author of Guided Practice in Mentoring and the Working Temperament Survey.</p>
    </article>

    <article class="staff-card" style="left:186px; top:183px;">
      <div class="staff-photo" role="img" aria-label="Portrait of the finance lead" style="background:linear-gradient(160deg,#c9c4b8,#8f8778);"></div>
      <h2 class="staff-role">Finance</h2>
      <p class="staff-name">Laura Penwick</p>
      <p class="staff-bio">Laura Penwick was employed for 21 years by the federal defense service, where she was awarded an Air Force Commendation Medal and the Inspector General's Professional Performer Award.</p>
    </article>

    <article class="staff-card" style="left:347px; top:183px;">
      <div class="staff-photo" role="img" aria-label="Portrait of the administration lead" style="background:linear-gradient(160deg,#6f7a3c,#a86a45);"></div>
      <h2 class="staff-role">Administration</h2>
      <p class="staff-name">Karen Holloway</p>
      <p class="staff-bio">Karen Holloway has been CEO of an Integrative Medical Oncology Center, vice president of operations and human resources for a Washington State production and manufacturing company.</p>
    </article>

    <article class="staff-card" style="left:28px; top:438px;">
      <div class="staff-photo" role="img" aria-label="Portrait of the media lead" style="background:linear-gradient(160deg,#2f7fb3,#6a4a3e);"></div>
      <h2 class="staff-role">Media</h2>
      <p class="staff-name">Sonia Caldwell</p>
      <p class="staff-bio">Sonia Caldwell is the founder and producer of Open Voices Radio. She is the author of Still Here – A Doubter's Journey Through Loss, which encourages readers to ease the fear of death, move through grief, and make the most of their lives every day.</p>
    </article>

    <article class="staff-card" style="left:186px; top:438px;">
      <div class="staff-photo" role="img" aria-label="Portrait of the education lead" style="background:linear-gradient(160deg,#3b3530,#9c7d68);"></div>
      <h2 class="staff-role">Education</h2>
      <p class="staff-name">Ray Whitfield</p>
      <p class="staff-bio">Ray is a history, civics, and language arts elementary school teacher. He is a graduate of Lakeview State University with a BA in English, language arts, and teacher education.</p>
    </article>

    <article class="staff-card" style="left:347px; top:438px;">
      <div class="staff-photo" role="img" aria-label="Collection of published book covers" style="background:linear-gradient(135deg,#2f5fa6,#c8762e 55%,#2c5a9a);"></div>
      <h2 class="staff-role">Publications</h2>
      <p class="staff-name">Clear Horizon Press</p>
      <p class="staff-bio">Clear Horizon Press is a wholly owned publisher that specializes in publishing books by emerging authors in afterlife studies, research, and education.</p>
    </article>

    <span class="footer-url" style="left:26px;">www.brightmeadowcivic.org</span>
    <svg class="footer-bar" style="left:118px;" width="367" height="16" viewBox="0 0 367 16">
      <polygon points="6,0 367,0 367,16 0,16" fill="#3a3891"/>
    </svg>
  </section>

  <!-- Programme page -->
  <section class="page programme-page">
    <div class="hero-photo" role="img" aria-label="Hands typing on a laptop beside a newspaper, notebook and coffee cup"></div>
    <svg class="hero-banner" width="525" height="126" viewBox="0 0 525 126">
      <polygon points="141,0 525,0 525,124 175,124" fill="#3a3891"/>
    </svg>
    <h2 class="hero-heading">
      <span class="lead">Teaching People to Have</span>
      <span class="strong">Afterlife Connections</span>
    </h2>

    <p class="programme-copy">Martin Ellery, president of BMCI, has developed an online training program that enables anyone to connect with loved ones living on the next plane of life. It uses a form of self-relaxation to bring the experiencer into a state in which the connections may occur. It then teaches the experiencer how to allow free, open unfoldment so messages can come through from the loved one. The experiencers fill out journals after each stage that are submitted to BMCI. Martin reads each journal and coaches experiencers to help them learn how to have an afterlife connection by allowing free unfoldment.</p>

    <p class="link-heading">The procedure is free on the Internet at this link:</p>
    <p class="link-sub">Open Horizon Connection Course</p>

    <div class="topic" style="left:34px; top:541px;">
      <svg width="30" height="30" viewBox="0 0 30 30"><rect x="6" y="6" width="18" height="18" transform="rotate(45 15 15)" fill="none" stroke="#3a3891" stroke-width="1.6"/><path d="M11 20h8M15 9v11M12 13h6" stroke="#3a3891" stroke-width="1.6" fill="none"/></svg>
      <span>Successes and Validations</span>
    </div>
    <div class="topic" style="left:34px; top:580px;">
      <svg width="30" height="30" viewBox="0 0 30 30"><rect x="6" y="6" width="18" height="18" transform="rotate(45 15 15)" fill="none" stroke="#3a3891" stroke-width="1.6"/><circle cx="12" cy="13" r="2" fill="#3a3891"/><circle cx="18" cy="13" r="2" fill="#3a3891"/><path d="M9 20q3-4 6 0q3-4 6 0" stroke="#3a3891" stroke-width="1.6" fill="none"/></svg>
      <span>Example Account by an Experiencer</span>
    </div>
    <div class="topic" style="left:34px; top:620px;">
      <svg width="30" height="30" viewBox="0 0 30 30"><rect x="6" y="6" width="18" height="18" transform="rotate(45 15 15)" fill="none" stroke="#3a3891" stroke-width="1.6"/><text x="15" y="19" text-anchor="middle" font-size="11" font-weight="700" fill="#3a3891" font-family="Titillium Web, sans-serif">$</text></svg>
      <span>Future Advancements with Funding</span>
    </div>
    <div class="topic" style="left:34px; top:655px;">
      <svg width="30" height="30" viewBox="0 0 30 30"><rect x="6" y="6" width="18" height="18" transform="rotate(45 15 15)" fill="none" stroke="#3a3891" stroke-width="1.6"/><circle cx="15" cy="15" r="4" fill="none" stroke="#3a3891" stroke-width="1.6"/><circle cx="15" cy="15" r="1.3" fill="#3a3891"/></svg>
      <span>Costs</span>
    </div>

    <div class="topic" style="left:253px; top:541px;">
      <svg width="30" height="30" viewBox="0 0 30 30"><rect x="6" y="6" width="18" height="18" transform="rotate(45 15 15)" fill="none" stroke="#3a3891" stroke-width="1.6"/><path d="M10 15a5 5 0 0 1 9-3M20 15a5 5 0 0 1-9 3" stroke="#3a3891" stroke-width="1.6" fill="none"/></svg>
      <span>Details about the Open<br>Horizon Connection Course</span>
    </div>
    <div class="topic" style="left:253px; top:584px;">
      <svg width="30" height="30" viewBox="0 0 30 30"><rect x="6" y="6" width="18" height="18" transform="rotate(45 15 15)" fill="none" stroke="#3a3891" stroke-width="1.6"/><path d="M11 20v-4M14 20v-7M17 20v-5M20 20v-3M10 20h11" stroke="#3a3891" stroke-width="1.6" fill="none"/></svg>
      <span>Project Results</span>
    </div>
    <div class="topic" style="left:253px; top:628px;">
      <svg width="30" height="30" viewBox="0 0 30 30"><rect x="6" y="6" width="18" height="18" transform="rotate(45 15 15)" fill="none" stroke="#3a3891" stroke-width="1.6"/><circle cx="15" cy="15" r="5" fill="none" stroke="#3a3891" stroke-width="1.4"/><path d="M15 12v3h2.5" stroke="#3a3891" stroke-width="1.4" fill="none"/></svg>
      <span>Timeline</span>
    </div>

    <svg class="footer-bar" style="left:29px;" width="380" height="16" viewBox="0 0 380 16">
      <polygon points="0,0 374,0 380,16 0,16" fill="#3a3891"/>
    </svg>
    <span class="footer-url" style="left:416px;">www.brightmeadowcivic.org</span>
  </section>

</div>
</body>
</html>
```